Vesta PR Website

Vesta PR are a PR company with a requirement for a new website. In consultation with the client, we have defined a wireframe for a homepage to show content and functionality. A PDF of the wire frame is attached.
Current site http://www.vesta-pr.co.uk/
Updates
If you are using Stock Photography - please use iStock
Dear All
Unfortunately, my client didn't like any of the designs submitted.
I've uploaded 3 examples of the type of photography that will appear in the carousel as supplied by the client.
Target Market(s)
Business to Business/Professionals - high value clients
Number of Pages Required
1 page
Requirements
Must have
- Colour scheme is attached as a .ase file from Kuler and can be viewed on Kuler if you search for 'VESTA PR Palette'
Corporate Typeface is Futura Book - use of Cufon is OK
Current Logo to be reatainedCall 2 Action Buttons will be controlled via the CMS so a generic background may be useful for these.
Nice to have
- RSS feeds

```html
<!DOCTYPE html>
<html lang="en">
<head>
<meta charset="utf-8">
<title>Vesta PR – Home</title>
<link rel="stylesheet" href="https://fonts.googleapis.com/css2?family=Jost:wght@400;500&family=Noto+Sans:wght@400;700&display=swap">
<style>
  :root {
    --teal-deep: #0a6378;
    --teal-dark: #0c7489;
    --teal: #129d8c;
    --teal-light: #46b8a8;
    --hero: #2ca899;
    --aqua: #a8e0d8;
    --aqua-soft: #c9ece6;
    --panel: #f2f2f2;
    --tab: #ececec;
    --ink: #4d4d4d;
    --white: #ffffff;
  }
  * { margin: 0; padding: 0; box-sizing: border-box; }
  html, body { width: 754px; height: 1200px; overflow: hidden; background: var(--white); }
  body { position: relative; font-family: "Noto Sans", Verdana, sans-serif; color: var(--ink); }
  .page { position: absolute; left: 6px; top: 0; width: 743px; height: 1200px; background: var(--white); box-shadow: 0 0 4px rgba(0,0,0,.12); }
  .abs { position: absolute; }

  /* header */
  .brand { left: 16px; top: 24px; font-family: "Jost", sans-serif; font-size: 30px; font-weight: 400; letter-spacing: 5px; color: var(--teal-dark); display: flex; align-items: center; gap: 10px; }
  .brand-mark { width: 14px; height: 14px; background: var(--aqua); }
  .call { right: 14px; top: 30px; font-family: "Jost", sans-serif; font-size: 20px; color: var(--teal-deep); }
  .contact-row { right: 16px; top: 61px; display: flex; align-items: center; gap: 14px; font-size: 8.5px; font-weight: 700; color: var(--teal-deep); }
  .contact-row .social { font-family: "Jost", sans-serif; font-size: 11px; font-weight: 500; color: var(--teal-light); }

  /* nav */
  .nav { left: 0; top: 81px; width: 743px; height: 35px; background: linear-gradient(var(--teal) 0 24px, var(--white) 24px 25px, var(--teal-light) 25px); }
  .nav ul { list-style: none; display: flex; justify-content: center; height: 24px; align-items: center; font-family: "Jost", sans-serif; font-size: 11px; font-weight: 500; color: var(--white); text-shadow: 0 1px 1px rgba(0,0,0,.35); }
  .nav li + li::before { content: "|"; margin: 0 13px; }

  /* hero */
  .hero { left: 0; top: 117px; width: 743px; height: 250px; background: var(--hero); }
  .hero-copy { left: 16px; top: 15px; width: 344px; height: 221px; background: rgba(200,236,231,.85); padding: 13px 12px 0 12px; color: var(--teal-dark); font-size: 9.4px; line-height: 13.6px; }
  .hero-copy h1 { font-family: "Jost", sans-serif; font-weight: 400; font-size: 18px; color: var(--teal-deep); margin-bottom: 8px; }
  .hero-copy .rule { margin: 11px 0 12px; letter-spacing: -0.4px; overflow: hidden; white-space: nowrap; }
  .hero-copy .more { position: absolute; right: 13px; bottom: 6px; font-weight: 700; text-decoration: underline; }
  .hero-photo { left: 386px; top: 3px; width: 352px; height: 240px; background: linear-gradient(100deg, var(--hero) 0%, #8fcfc5 45%, #e9ecec 80%, #f6f6f6 100%); }

  /* tabs */
  .tab { top: 368px; width: 135px; height: 44px; background: linear-gradient(#f8f8f8, var(--tab)); box-shadow: 0 1px 2px rgba(0,0,0,.15); font-family: "Jost", sans-serif; font-size: 12px; color: var(--teal-deep); display: flex; align-items: center; justify-content: center; text-align: center; }
  .tab.active { top: 354px; left: 16px; height: 58px; background: linear-gradient(var(--teal-dark), var(--teal-deep)); color: var(--white); font-size: 13px; line-height: 15px; box-shadow: 0 3px 4px rgba(0,0,0,.3); }

  /* welcome */
  .welcome { left: 16px; top: 432px; width: 458px; font-size: 9.3px; line-height: 11px; color: #555; }
  .welcome h2 { font-family: "Jost", sans-serif; font-weight: 400; font-size: 23px; color: var(--teal-deep); margin-bottom: 14px; }
  .welcome p { margin-bottom: 11px; }
  .divider { left: 488px; top: 426px; height: 516px; border-left: 1px dotted #bbb; }

  /* feature boxes */
  .feature { width: 454px; height: 131px; background: var(--panel); }
  .feature h3 { height: 31px; background: linear-gradient(var(--teal-dark), var(--teal-deep)); color: var(--white); font-family: "Jost", sans-serif; font-weight: 400; font-size: 18px; padding: 3px 12px; }
  .feature .body { position: absolute; left: 13px; top: 35px; width: 330px; font-size: 8.2px; line-height: 9.8px; color: #555; }
  .feature .dots { margin: 8px 0 9px; overflow: hidden; white-space: nowrap; letter-spacing: 0.5px; }
  .feature .more { position: absolute; left: 310px; top: 83px; font-size: 7px; font-weight: 700; text-decoration: underline; }
  .feature .photo { left: 366px; top: 38px; width: 76px; height: 84px; background: linear-gradient(#b9a58e, #6b5a4a); border: 1px solid #ddd; }

  /* call to action */
  .cta { left: 503px; width: 226px; height: 84px; }
  .cta-band { position: absolute; left: 41px; top: 1px; right: 0; height: 81px; background: linear-gradient(var(--teal-dark), var(--teal-deep)); box-shadow: 2px 3px 3px rgba(0,0,0,.3); }
  .cta-dot { position: absolute; left: 0; top: 0; width: 83px; height: 83px; border-radius: 50%; background: var(--aqua); }
  .cta-label { position: absolute; left: 86px; top: 25px; font-family: "Jost", sans-serif; font-size: 23px; color: var(--white); white-space: nowrap; }

  /* footer */
  .footer { left: 0; top: 982px; width: 743px; height: 184px; background: var(--aqua); }
  .footer-band { height: 40px; background: linear-gradient(var(--teal-dark), var(--teal-deep)); }
  .footer-col { top: 10px; }
  .footer-col h4 { font-size: 14px; font-weight: 700; color: var(--white); margin-bottom: 21px; }
  .footer-col ul { list-style: none; }
  .footer-col li { font-size: 8.7px; font-weight: 700; color: var(--teal-deep); letter-spacing: .6px; line-height: 18px; }
  .signup p { font-size: 8.3px; font-weight: 700; color: var(--teal-deep); letter-spacing: .4px; line-height: 10.5px; margin-top: -7px; }
  .signup .field { margin-top: 11px; width: 197px; height: 29px; background: var(--white); border: 1px solid var(--teal-dark); font-size: 9px; font-weight: 700; color: var(--teal-deep); padding: 8px 7px; }
  .signup .button { margin-top: 10px; width: 94px; height: 21px; border-radius: 3px; background: linear-gradient(var(--teal-dark), var(--teal-deep)); color: var(--white); font-size: 11px; text-align: center; line-height: 21px; }

  .bottom-bar { left: 0; top: 1166px; width: 743px; height: 34px; background: linear-gradient(var(--teal) 0 27px, var(--teal-light) 27px); color: var(--white); font-size: 8.5px; font-weight: 700; letter-spacing: .5px; }
  .bottom-bar .legal { position: absolute; left: 18px; top: 10px; }
  .bottom-bar .links { position: absolute; right: 16px; top: 10px; word-spacing: 2px; }
</style>
</head>
<body>
<div class="page">

  <header>
    <div class="abs brand"><span>Vesta PR</span><span class="brand-mark"></span></div>
    <div class="abs call">Call us now 0141 555 0199</div>
    <div class="abs contact-row">
      <span>Email Us:</span>
      <span class="social">Talkwire</span>
      <span class="social">Chirpline</span>
      <span class="social">Pagebook</span>
    </div>
  </header>

  <nav class="abs nav">
    <ul>
      <li>Homes</li><li>Vesta Services</li><li>Press Office</li><li>Vesta Case Studies</li>
      <li>Vesta People</li><li>Blog</li><li>Vesta News</li><li>Contact Us</li>
    </ul>
  </nav>

  <section class="abs hero">
    <div class="abs hero-copy">
      <h1>Online Public Relations</h1>
      <p>Lorem Ipsum is simply dummy text of the printing and typesetting industry. Lorem Ipsum has been the industry's standard dummy text ever since the 1500s.</p>
      <p class="rule">================================================</p>
      <p>When an unknown printer took a galley of type and scrambled it to make a type specimen book. It has survived not only five centuries, but also the leap into electronic typesetting, remaining essentially unchanged.</p>
      <span class="more">View More</span>
    </div>
    <div class="abs hero-photo" role="img" aria-label="Photo of a customer service team wearing headsets at their desks"></div>
  </section>

  <div class="abs tab active">ONLINE PUBLIC<br>RELATIONS</div>
  <div class="abs tab" style="left:165px">Media Relations</div>
  <div class="abs tab" style="left:310px">Consumer Campaigns</div>
  <div class="abs tab" style="left:452px">Crisis Public Relations</div>
  <div class="abs tab" style="left:595px">Internal Communication</div>

  <main>
    <section class="abs welcome">
      <h2>Welcome to Vesta PR</h2>
      <p>Vesta Public Relations is one of Scotland’s leading independent agencies. Founded in 2000, we were determined to create a public relations service with a real difference – hence the name.</p>
      <p>Vesta Public Relation's trademark is a fresh, creative and hard working approach to public relations. It is an approach that secures real results for our clients.</p>
      <p>We are an agency with intelligence, integrity and imagination offering a comprehensive, results driven public relations service covering traditional and online public relations strategy and support.</p>
      <p>Lorem Ipsum is simply dummy text of the printing and typesetting industry. Lorem Ipsum has been the industry's standard dummy text ever since the 1500s.</p>
    </section>

    <section class="abs feature" style="left:16px; top:633px">
      <h3>Client News</h3>
      <div class="body">
        <p>Phasellus sapien ipsum, interdum ut dapibus in, hendrerit nec nulla. Donec egestas scelerisque metus, nec placeratlectus ultrices ac. Nam sodales mollis euismod. Mauris ornare viverra dignissim.</p>
        <p class="dots">........................................................................</p>
        <p>egestas scelerisque metus, nec placeratlectus ultrices ac. Nam sodales mollis euismod. Mauris ornare viverra dignissi</p>
      </div>
      <span class="abs more" style="left:323px">More</span>
      <div class="abs photo" role="img" aria-label="Portrait photo of a smiling client"></div>
    </section>

    <section class="abs feature" style="left:14px; top:792px">
      <h3>Latest Blog Entries</h3>
      <div class="body">
        <p>Phasellus sapien ipsum, interdum ut dapibus in, hendrerit nec nulla. Donec egestas scelerisque metus, nec placeratlectus ultrices ac. Nam sodales mollis euismod. Mauris ornare viverra dignissim.</p>
        <p class="dots">........................................................................</p>
        <p>egestas scelerisque metus, nec placeratlectus ultrices ac. Nam sodales mollis euismod. Mauris ornare viverra dignissi</p>
      </div>
      <span class="abs more" style="left:323px">More</span>
      <div class="abs photo" role="img" aria-label="Portrait photo of a blog author in glasses" style="background:linear-gradient(#e8e4dc,#4a4a4a)"></div>
    </section>

    <div class="abs divider"></div>

    <aside>
      <div class="abs cta" style="top:472px"><div class="cta-band"></div><div class="cta-dot"></div><span class="cta-label">Call 2 Action</span></div>
      <div class="abs cta" style="top:585px"><div class="cta-band"></div><div class="cta-dot"></div><span class="cta-label">Call 2 Action</span></div>
      <div class="abs cta" style="top:698px"><div class="cta-band"></div><div class="cta-dot"></div><span class="cta-label">Call 2 Action</span></div>
      <div class="abs cta" style="top:819px"><div class="cta-band"></div><div class="cta-dot"></div><span class="cta-label">Call 2 Action</span></div>
    </aside>
  </main>

  <footer class="abs footer">
    <div class="footer-band"></div>
    <div class="abs footer-col" style="left:17px">
      <h4>Services</h4>
      <ul><li>Online Public Relations</li><li>Media Relations</li><li>Consumer Campaigns</li><li>Crisis Public Relations</li><li>Internal Communications</li></ul>
    </div>
    <div class="abs footer-col" style="left:201px">
      <h4>Links</h4>
      <ul><li>Subscribe to RSS Feed</li><li>Our Pagebook page</li><li>Link Three</li><li>Link Four</li></ul>
    </div>
    <div class="abs footer-col" style="left:364px">
      <h4>About Us</h4>
      <ul><li>About Company</li><li>Company Profile</li><li>Link 1</li><li>Link2</li></ul>
    </div>
    <div class="abs footer-col signup" style="left:527px">
      <h4>E-News Sign Up</h4>
      <p>Subscribe to our Newsletter to<br>recieve news about Our Services,<br>Products and Events.</p>
      <div class="field">Email Address</div>
      <div class="button">Subscribe</div>
    </div>
  </footer>

  <div class="abs bottom-bar">
    <span class="legal">© Copyright Notice | Site Credit | Legal</span>
    <span class="links">Home &nbsp;| &nbsp;About Us &nbsp;| &nbsp;Services &nbsp;| &nbsp;Blog &nbsp;| &nbsp;Contact Us</span>
  </div>

</div>
</body>
</html>
```